Small Business Broker Business Card Design

A business card design for a small business brokerage, which is a financial service, not unlike real estate brokerage, but for small businesses such as laundromats, pizza shops, restaurants, cleaners etc. The designs should all be simple, more conservative in nature, using the colors and font of the logo. Again, think real estate Brokerage as a business context
Contact Information for Business Card
Name: Glen R. Harlow. Title: Small Business Advisor. Email: g.harlow@bayfieldcapitalworks.example. Mobile: (555) 274-3918. Office: (555) 806-2147. www.bayfieldcapitalworks.example

```html
<!DOCTYPE html>
<html lang="en">
<head>
<meta charset="utf-8">
<title>Bayfield Capital Works – Business Card</title>
<link href="https://fonts.googleapis.com/css2?family=Montserrat:wght@600;700&family=Poppins:wght@400;500&display=swap" rel="stylesheet">
<style>
  :root {
    --navy: #1a3866;
    --navy-soft: #2a4b80;
    --green: #7cc242;
    --paper: #f3f3f2;
    --white: #ffffff;
    --backdrop: #1b1b1b;
  }
  * { margin: 0; padding: 0; box-sizing: border-box; }
  html, body { width: 1200px; height: 1059px; overflow: hidden; background: var(--backdrop); }
  .canvas { position: relative; width: 1200px; height: 1059px; }

  .card { position: absolute; border-radius: 24px; overflow: hidden; }

  /* Front */
  .card-front { left: 257px; top: 89px; width: 687px; height: 390px; background: var(--paper); }
  .front-wave { position: absolute; inset: 0; width: 100%; height: 100%; }
  .brand-block { position: absolute; left: 30px; top: 34px; width: 316px; text-align: center; }
  .brand-square { display: block; width: 58px; height: 58px; margin: 0 auto 30px; background: var(--navy); }
  .brand-name {
    font-family: 'Montserrat', sans-serif; font-weight: 700; font-size: 17.5px;
    color: var(--navy); white-space: nowrap; letter-spacing: 0.1px;
  }
  .brand-tagline {
    font-family: 'Montserrat', sans-serif; font-weight: 600; font-size: 8.6px;
    color: var(--green); letter-spacing: 1.25px; white-space: nowrap; margin-top: 3px;
  }
  .person { position: absolute; right: 35px; top: 188px; text-align: right; }
  .person-name {
    font-family: 'Montserrat', sans-serif; font-weight: 700; font-size: 25px;
    color: var(--green); line-height: 1; text-transform: uppercase;
  }
  .person-title {
    font-family: 'Poppins', sans-serif; font-weight: 400; font-size: 16px;
    color: var(--white); margin-top: 6px;
  }
  .contact-list { position: absolute; right: 33px; top: 256px; list-style: none; }
  .contact-item {
    display: flex; align-items: center; justify-content: flex-end; gap: 7px;
    font-family: 'Poppins', sans-serif; font-size: 16px; color: var(--white);
    height: 24.5px;
  }
  .contact-icon { width: 12px; height: 12px; fill: var(--green); flex: none; }

  /* Back */
  .card-back { left: 254px; top: 547px; width: 693px; height: 393px; background: var(--navy); }
  .back-brand {
    position: absolute; left: 0; right: 0; top: 150px; text-align: center;
    font-family: 'Montserrat', sans-serif; font-weight: 700; font-size: 30px;
    color: var(--navy-soft); letter-spacing: 1px;
  }
  .back-url {
    position: absolute; left: 0; right: 0; top: 334px; text-align: center;
    font-family: Arial, Helvetica, sans-serif; font-size: 18px; letter-spacing: 1.4px;
    color: var(--white);
  }
  .back-url .domain { color: var(--green); }
</style>
</head>
<body>
<main class="canvas">

  <section class="card card-front" aria-label="Business card front">
    <svg class="front-wave" viewBox="0 0 1168 663" preserveAspectRatio="none" aria-hidden="true">
      <path fill="var(--navy)" d="M0 393 C90 460 170 500 270 495 C480 485 700 200 960 186 C1060 182 1130 225 1168 258 V663 H0 Z"/>
      <path fill="var(--green)" d="M175 470 C420 505 660 200 960 172 C1000 169 1035 172 1062 180 C1030 176 995 176 960 180 C690 212 440 498 175 470 Z"/>
    </svg>

    <div class="brand-block">
      <span class="brand-square"></span>
      <p class="brand-name">BAYFIELD CAPITAL WORKS, INC</p>
      <p class="brand-tagline">CONFIDENTLY BUY OR SELL A LOCAL BUSINESS TODAY</p>
    </div>

    <div class="person">
      <h1 class="person-name">Glen R. Harlow</h1>
      <p class="person-title">Small Business Advisor</p>
    </div>

    <ul class="contact-list">
      <li class="contact-item">(555) 806-2147
        <svg class="contact-icon" viewBox="0 0 12 12" aria-hidden="true"><path d="M1 4 C1 2 3 1.5 6 1.5 S11 2 11 4 V5 H8.5 V3.8 H3.5 V5 H1 Z M3 5.5 H9 L10.5 10.5 H1.5 Z"/></svg>
      </li>
      <li class="contact-item">(555) 274-3918
        <svg class="contact-icon" viewBox="0 0 12 12" aria-hidden="true"><path d="M3 0.5 H9 V11.5 H3 Z M4 1.8 V9 H8 V1.8 Z M5.5 9.7 H6.5 V10.6 H5.5 Z"/></svg>
      </li>
      <li class="contact-item">g.harlow@bayfieldcapitalworks.example
        <svg class="contact-icon" viewBox="0 0 12 12" aria-hidden="true"><path d="M6 0.8 L11.5 4.8 V11.2 H0.5 V4.8 Z M1.6 5.4 L6 8.6 L10.4 5.4 L6 2.2 Z"/></svg>
      </li>
      <li class="contact-item">www.bayfieldcapitalworks.example
        <svg class="contact-icon" viewBox="0 0 12 12" aria-hidden="true"><circle cx="6" cy="6" r="5.5"/><path fill="var(--navy)" d="M3 3.5 C4.5 3 5 4.5 4 5.5 C3.5 6.5 4.5 7.5 3.5 8.5 C2.5 7.5 2 5 3 3.5 Z M7 6 C8.5 5.5 9.5 7 8.5 9 C7.5 8.5 6.5 7.5 7 6 Z"/></svg>
      </li>
    </ul>
  </section>

  <section class="card card-back" aria-label="Business card back">
    <p class="back-brand">BAYFIELD CAPITAL WORKS</p>
    <p class="back-url">www.<span class="domain">bayfieldcapitalworks</span>.example</p>
  </section>

</main>
</body>
</html>
```